New letter head for Air Conditioning business

We need a new professional letter head design to suit our new re-branded air conditioning business. Our new logo is attached

```html
<!DOCTYPE html>
<html lang="en">
<head>
<meta charset="UTF-8">
<title>Norvane Letterhead</title>
<link href="https://fonts.googleapis.com/css2?family=Poppins:ital,wght@0,400;0,500;0,600;0,700;1,400&display=swap" rel="stylesheet">
<style>
  :root {
    --bg: #c9dcd2;
    --paper: #ffffff;
    --ink: #3b3b3d;
    --body: #5b5b5e;
    --green: #5bbf7e;
    --coral: #f06b5b;
    --sig-tone: #d9dadb;
  }
  * { margin: 0; padding: 0; box-sizing: border-box; }
  html, body {
    width: 1200px; height: 900px; overflow: hidden;
    background: var(--bg);
    font-family: "Poppins", sans-serif;
  }
  .letterhead {
    position: absolute; left: 296px; top: 20px;
    width: 608px; height: 860px;
    background: var(--paper);
    padding: 44px 48px 0 52px;
    color: var(--body);
  }
  .header { display: flex; justify-content: space-between; align-items: flex-start; }
  .brand { display: flex; align-items: center; gap: 12px; padding-top: 6px; }
  .brand-dot { width: 34px; height: 34px; border-radius: 50%; background: var(--green); }
  .brand-name {
    font-weight: 700; font-size: 30px; letter-spacing: 3px;
    color: var(--ink); line-height: 1;
  }
  .brand-tagline {
    font-weight: 600; font-size: 6.5px; letter-spacing: 1.6px;
    color: var(--green); margin-top: 5px; text-transform: uppercase;
  }
  .contact {
    border-left: 1.5px solid var(--green);
    padding-left: 10px;
    font-size: 9.5px; font-style: italic; line-height: 1.35;
    color: var(--ink);
  }
  .contact-address { margin-bottom: 7px; }
  .contact-line { display: flex; align-items: center; gap: 6px; }
  .contact-line svg { width: 8px; height: 8px; flex: none; }
  .greeting {
    margin-top: 120px; font-weight: 600; font-size: 11px; color: var(--ink);
  }
  .date {
    text-align: right; font-style: italic; font-size: 8.5px; margin-top: 2px;
  }
  .body-text p {
    font-size: 8.4px; line-height: 1.45; text-align: justify;
    margin-top: 12px;
  }
  .body-text p:first-child { margin-top: 4px; }
  .closing {
    margin-top: 20px; font-weight: 600; font-size: 11px; color: var(--ink);
  }
  .signature {
    margin-top: 12px; width: 96px; height: 34px;
    background: linear-gradient(90deg, var(--sig-tone), #eeeeef);
    border-radius: 4px;
  }
</style>
</head>
<body>
  <main class="letterhead">
    <header class="header">
      <div class="brand">
        <span class="brand-dot"></span>
        <div>
          <div class="brand-name">NORVANE</div>
          <div class="brand-tagline">Air Conditioning &amp; Refrigeration</div>
        </div>
      </div>
      <address class="contact">
        <div class="contact-address">PO Box 8800 Subville St00<br>Sample City Country 6103</div>
        <div class="contact-line">
          <svg viewBox="0 0 10 10"><path d="M2 1l2 2-1 1.2a6 6 0 0 0 2.8 2.8L7 6l2 2-1.2 1.4C4.5 9 1 5.5.6 2.2z" fill="var(--coral)"/></svg>
          000 000-0000
        </div>
        <div class="contact-line">
          <svg viewBox="0 0 10 10"><rect x="0.5" y="2" width="9" height="6.5" fill="var(--coral)"/><path d="M0.5 2l4.5 3.5L9.5 2" stroke="#fff" stroke-width="0.8" fill="none"/></svg>
          info@anydomain.com
        </div>
        <div class="contact-line">
          <svg viewBox="0 0 10 10"><circle cx="5" cy="5" r="4.5" fill="var(--coral)"/><path d="M5 .5v9M.5 5h9" stroke="#fff" stroke-width="0.7"/></svg>
          www.anydomain.com
        </div>
      </address>
    </header>

    <p class="greeting">Dear Hartley,</p>
    <p class="date">30 January 2080</p>

    <section class="body-text">
      <p>Lorem ipsum dolor sit amet, consectetuer adipiscing elit, sed diam nonummy nibh euismod tincidunt ut laoreet dolore magna aliquam erat volutpat. Ut wisi enim ad minim commodo consequat. Duis dolore te feugait nulla facilisi. Nam liber tempor cum soluta nobis eleifendu Lorem ipsum dolor sit amet, consectetuer adipiscing elit, sed diam nonummy nibh euismod consequat. Duis dolore te feugait nulla facilisi. Nam liber tempor cum soluta nobis eleifendu euismod tincidunt ut laoreet dolore magna aliquam erat volutpat. Ut wisi enim ad minimoa</p>
      <p>Consectetuer adipiscing elit, sed diam nonummy nibh euismod tincidunt utom laoreet dolore magna aliquam erat volutpat. Ut wisi enim ad minim veniam, quis nostrud exercilmo Consectetuer adipiscing elit, sed diam nonummy nibh euismod tincidunt utom laoreet dolore magna aliquam erat volutpat. Ut wisi enim ad minim veniam, quis nostrud exerci tation ullamcorper nisl suscipit lobortis nisl utiliomu aliquip ex ea commod uconse qualitmu</p>
      <p>tincidunt ut laoreet dolore magna aliquam erat volutpat. Ut wisi enim ad minim commodo consequat. Duis dolore te feugait nulla facilisi. Nam liber tempor cum soluta nobis eleifendu Lorem ipsum dolor sit amet, consectetuer adipiscing elit, sed diam nonummy nibh euismod tincidunt ut laoreet dolore magna aliquam erat volutpat. Ut wisi enim ad minim commodnconsequat. Duis dolore te feugait nulla facilisi. Nam liber tempor cum soluta nobineleifendu euismod tincidunt ut laoreet dolore magna aliquam erat volutpat. Ut wisims</p>
    </section>

    <p class="closing">Sincerely Yours</p>
    <div class="signature" role="img" aria-label="Handwritten signature of the sender"></div>
  </main>
</body>
</html>
```